Letter head / email signature/ contract document templates

We need a professional email signature and letterhead designed for our established carpentry and maintenance company. Our Logo (attached) was originally designed 6 years ago by design guru and we love it, looking for something to compliment it ( not a home job)

```html
<!DOCTYPE html>
<html lang="en">
<head>
<meta charset="utf-8">
<title>Harbourline Fix – Stationery</title>
<link href="https://fonts.googleapis.com/css2?family=Raleway:wght@400;500;600;700;800&display=swap" rel="stylesheet">
<style>
  :root{
    --red:#e31e24;
    --charcoal:#3a3a3a;
    --ink:#2b2b2b;
    --grey-bg:#e6e7e9;
    --grey-band:#ededee;
    --paper:#ffffff;
    --muted:#555;
  }
  *{box-sizing:border-box;margin:0;padding:0}
  html,body{width:1200px;height:2238px;overflow:hidden}
  body{position:relative;background:var(--grey-bg);font-family:"Raleway",sans-serif;color:var(--ink)}
  .band{position:absolute;left:0;top:800px;width:1200px;height:795px;background:var(--grey-band)}

  .brand{font-family:"Raleway",sans-serif;font-weight:800;display:inline-flex;align-items:center;gap:.35em;white-space:nowrap}
  .brand .mark{width:.5em;height:.5em;background:var(--red);display:inline-block}

  /* folder cover */
  .folder{position:absolute;left:164px;top:112px;width:412px;height:573px;background:var(--charcoal);box-shadow:0 6px 14px rgba(0,0,0,.18)}
  .folder .brand{position:absolute;left:0;right:0;top:255px;justify-content:center;color:#fff;font-size:36px}
  .folder .web{position:absolute;left:0;right:0;bottom:33px;text-align:center;color:#fff;font-size:8px}
  .folder .web span{color:var(--red)}

  /* letterhead */
  .letterhead{position:absolute;left:618px;top:112px;width:402px;height:573px;background:var(--paper);box-shadow:0 6px 14px rgba(0,0,0,.12)}
  .rule-bar{position:absolute;left:-1px;top:0;width:6px;height:100%}
  .letterhead .brand{position:absolute;left:36px;top:56px;font-size:16px;color:var(--ink)}
  .lh-contact{position:absolute;right:36px;top:42px;font-size:6px;line-height:8px;color:var(--muted)}
  .lh-contact i{display:inline-block;width:5px;height:4px;background:var(--red);margin-right:2px;vertical-align:middle}
  .lh-body{position:absolute;left:32px;top:135px;width:338px;font-size:6.4px;line-height:10.8px;color:#444;text-align:justify}
  .lh-body p{margin-bottom:11px}

  /* envelopes */
  .env{position:absolute;background:var(--paper);box-shadow:0 6px 14px rgba(0,0,0,.12);overflow:hidden}
  .env-back{left:620px;top:880px;width:520px;height:248px}
  .env-back .flap{position:absolute;left:0;top:0;width:100%;height:64px;background:var(--red);display:flex;align-items:center;justify-content:center}
  .env-back .brand{color:#fff;font-size:22px}
  .env-back .brand .mark{background:#fff}
  .env-front{left:60px;top:1260px;width:520px;height:248px}
  .env-front .top-bar{position:absolute;left:0;top:2px;width:190px;height:5px}
  .env-front .brand{position:absolute;left:26px;top:30px;font-size:20px;color:var(--ink)}
  .env-front .addr{position:absolute;left:26px;top:68px;font-size:9px;line-height:13px;color:var(--muted)}
  .env-front .addr i{display:inline-block;width:6px;height:5px;background:var(--red);margin-right:4px;vertical-align:middle}
  .env-front .window{position:absolute;right:40px;bottom:30px;width:160px;height:68px;border:1px solid #d6d6d6;border-radius:6px;background:#f3f3f3}

  /* email signature */
  .signature{position:absolute;left:188px;top:1763px;width:824px;height:305px;background:var(--paper);box-shadow:0 6px 14px rgba(0,0,0,.2);overflow:hidden}
  .signature svg.sig-art{position:absolute;left:0;top:0}
  .sig-name{position:absolute;left:46px;top:44px;font-size:28px;font-weight:600;color:var(--charcoal)}
  .sig-role{position:absolute;left:46px;top:80px;font-size:23px;font-weight:500;color:var(--red)}
  .sig-details{position:absolute;left:46px;top:145px;font-size:18px;line-height:23.5px;color:var(--charcoal)}
  .sig-details .gap{height:10px}
  .sig-details i{display:inline-block;width:13px;height:11px;background:var(--red);margin-right:6px;vertical-align:-1px;border-radius:2px}
  .signature .brand{position:absolute;left:322px;top:206px;font-size:19px;color:var(--charcoal)}
  .social{position:absolute;left:518px;top:32px;display:flex;align-items:center;gap:7px}
  .social span{width:24px;height:24px;border-radius:50%;background:var(--red)}
  .social b{margin-left:6px;font-weight:500;font-size:19px;color:#fff}
</style>
</head>
<body>
  <div class="band"></div>

  <section class="folder">
    <div class="brand"><span class="mark"></span>Harbourline Fix</div>
    <div class="web">www.<span>harbourlinefix</span>.com</div>
  </section>

  <section class="letterhead">
    <svg class="rule-bar" viewBox="0 0 6 573" width="6" height="573" aria-hidden="true">
      <rect x="0" y="0" width="6" height="84" fill="#2b2b2b"/>
      <rect x="0" y="84" width="6" height="489" fill="#e31e24"/>
    </svg>
    <div class="brand"><span class="mark"></span>Harbourline Fix</div>
    <div class="lh-contact">
      48 Cedar Bend Road,<br>Maple Ridge, ON L5K 3P2<br>
      <i></i>555.210.4870<br><i></i>info@harbourlinefix.com<br><i></i>www.harbourlinefix.com
    </div>
    <div class="lh-body">
      <p>Dear customer,</p>
      <p>Thank you for choosing our team for your recent repair work. We take pride in careful carpentry, honest quotes and tidy job sites, and we aim to finish every project on schedule with clear updates from the first visit to the final walkthrough. Our crew arrives on time, protects your floors and furniture, and cleans up before leaving each day. If anything needs attention after we finish, simply call the office and we will book a return visit at no extra cost.</p>
      <p>Thank you for choosing our team for your recent repair work. We take pride in careful carpentry, honest quotes and tidy job sites, and we aim to finish every project on schedule with clear updates from the first visit to the final walkthrough. Our crew arrives on time, protects your floors and furniture, and cleans up before leaving each day. If anything needs attention after we finish, simply call the office and we will book a return visit at no extra cost.</p>
      <p>Thank you for choosing our team for your recent repair work. We take pride in careful carpentry, honest quotes and tidy job sites, and we aim to finish every project on schedule with clear updates from the first visit to the final walkthrough. Our crew arrives on time, protects your floors and furniture, and cleans up before leaving each day. If anything needs attention after we finish, simply call the office and we will book a return visit at no extra cost.</p>
      <p>Please keep this letter with your records, and contact our office if you have any questions about the work, the schedule or your invoice. We look forward to working with you again.</p>
      <p>Yours sincerely,</p>
    </div>
  </section>

  <section class="env env-back">
    <div class="flap"><div class="brand"><span class="mark"></span>Harbourline Fix</div></div>
  </section>

  <section class="env env-front">
    <svg class="top-bar" viewBox="0 0 190 5" width="190" height="5" aria-hidden="true">
      <rect x="0" y="0" width="146" height="5" fill="#e31e24"/>
      <rect x="146" y="0" width="44" height="5" fill="#2b2b2b"/>
    </svg>
    <div class="brand"><span class="mark"></span>Harbourline Fix</div>
    <div class="addr">
      48 Cedar Bend Road,<br>Maple Ridge, ON L5K 3P2<br>
      <i></i>555.210.4870<br><i></i>info@harbourlinefix.com<br><i></i>www.harbourlinefix.com
    </div>
    <div class="window"></div>
  </section>

  <section class="signature">
    <svg class="sig-art" viewBox="0 0 824 305" width="824" height="305">
      <defs>
        <linearGradient id="photoTone" x1="0" y1="0" x2="1" y2="1">
          <stop offset="0" stop-color="#6b6f78"/>
          <stop offset=".55" stop-color="#a08a72"/>
          <stop offset="1" stop-color="#d9b48c"/>
        </linearGradient>
      </defs>
      <polygon points="452,0 824,0 824,305 642,305" fill="url(#photoTone)" role="img" aria-label="Photo of gloved hands marking a timber board with a pencil and tape measure"/>
      <polygon points="384,0 452,0 642,305 574,305" fill="#e31e24"/>
    </svg>
    <div class="sig-name">TOMAS REEVE</div>
    <div class="sig-role">Director</div>
    <div class="sig-details">
      48 Cedar Bend Road,<br>Maple Ridge, ON L5K 3P2
      <div class="gap"></div>
      <i></i>555.210.4870<br><i></i>info@harbourlinefix.com<br><i></i>www.harbourlinefix.com
    </div>
    <div class="brand"><span class="mark"></span>Harbourline Fix</div>
    <div class="social"><span></span><span></span><span></span><b>@harbourlinefix</b></div>
  </section>
</body>
</html>
```